Tallowmere
Business cards/letter head
Tallowmere - Consulting
Use standard fonts
Nora Vambeck
4187 Larkwood Ave NE Seattle, WA 98115
Vambeck.nora@fenwistmail.com
please use a complementary font to the logo. logo art uploaded.

```html
<!DOCTYPE html>
<html lang="en">
<head>
<meta charset="utf-8">
<title>Tallowmere Stationery</title>
<link rel="stylesheet" href="https://fonts.googleapis.com/css2?family=Questrial&family=Open+Sans:wght@400;600;700&display=swap">
<style>
:root{
  --backdrop:#808183;
  --paper:#ffffff;
  --charcoal:#3b3c3e;
  --charcoal-deep:#2f3032;
  --map-tone:#4a4a3c;
  --sun:#e6d72b;
  --sun-soft:#efe36a;
  --ink:#6a6b6d;
  --ink-dark:#3d3e40;
  --line:#d9d9d9;
}
*{box-sizing:border-box;margin:0;padding:0}
html,body{width:1200px;height:1075px;overflow:hidden}
body{background:var(--backdrop);position:relative;font-family:"Open Sans",Arial,sans-serif;color:var(--ink)}
.piece{position:absolute;overflow:hidden;box-shadow:0 2px 6px rgba(0,0,0,.25)}
.piece svg.ring{position:absolute;left:0;top:0}
.logo{position:absolute;display:flex;align-items:center;gap:10px;font-family:"Questrial",Arial,sans-serif;color:var(--ink);letter-spacing:.5px;line-height:1;white-space:nowrap}
.logo .dot{border-radius:50%;background:var(--sun);flex:none}
.contact{position:absolute;font-size:10.5px;line-height:1.55;color:var(--ink);white-space:nowrap}

/* business card front */
.card-front{left:81px;top:66px;width:513px;height:288px;background:var(--paper)}
.card-front .logo{left:34px;top:58px;font-size:44px}
.card-front .logo .dot{width:14px;height:14px}
.card-front .holder{position:absolute;left:36px;top:212px;font-size:19px;font-weight:700;color:var(--ink-dark)}
.card-front .contact{left:345px;top:92px;font-size:10px}

/* business card back */
.card-back{left:615px;top:66px;width:510px;height:288px;background:var(--charcoal)}
.card-back .map{position:absolute;left:30px;top:20px;width:380px;height:230px;background:radial-gradient(ellipse at 45% 50%,var(--map-tone),var(--charcoal) 70%)}
.card-back .logo{right:40px;top:196px;font-size:40px;color:#ffffff}
.card-back .logo .dot{width:14px;height:14px}

/* letterhead */
.letterhead{left:81px;top:405px;width:513px;height:609px;background:var(--paper)}
.letterhead .logo{left:34px;top:44px;font-size:36px}
.letterhead .logo .dot{width:12px;height:12px}
.letter{position:absolute;left:36px;top:132px;width:410px;font-size:8.6px;line-height:1.55;color:var(--ink)}
.letter .recipient{margin-bottom:14px}
.letter p{margin-bottom:9px}
.signature{width:110px;height:26px;margin-top:6px;background:linear-gradient(90deg,#e4e4e4,#f3f3f3)}
.letterhead .contact{left:395px;top:540px;font-size:8px}

/* envelope back */
.envelope-back{left:615px;top:405px;width:510px;height:195px;background:var(--paper)}
.envelope-back .flap{position:absolute;left:0;top:0}
.envelope-back .dot{position:absolute;left:241px;top:44px;width:28px;height:28px;border-radius:50%;background:#ffffff}

/* envelope front */
.envelope-front{left:615px;top:615px;width:510px;height:230px;background:var(--paper)}
.envelope-front .logo{right:130px;top:142px;font-size:30px}
.envelope-front .logo .dot{width:10px;height:10px}

/* compliment card */
.compliment{left:615px;top:855px;width:510px;height:159px;background:var(--sun)}
.compliment .map{position:absolute;left:20px;top:10px;width:330px;height:140px;background:radial-gradient(ellipse at 45% 50%,var(--sun-soft),var(--sun) 70%)}
.compliment .logo{right:34px;top:92px;font-size:32px;color:var(--ink-dark)}
.compliment .logo .dot{width:11px;height:11px;background:#ffffff}
</style>
</head>
<body>

<section class="piece card-front" aria-label="Business card front">
  <svg class="ring" width="513" height="288" viewBox="0 0 513 288">
    <circle cx="430" cy="130" r="118" fill="none" stroke="var(--sun)" stroke-width="16" stroke-dasharray="70 10"/>
    <circle cx="430" cy="130" r="98" fill="#ffffff" stroke="var(--line)" stroke-width="1"/>
  </svg>
  <div class="logo"><span>tallowmere</span><span class="dot"></span></div>
  <div class="holder">Nora Vambeck</div>
  <div class="contact">
    4187 Larkwood Ave NE<br>Seattle, WA 98115<br><br>
    +1 (206) 555-0142<br>Vambeck.nora@fenwistmail.com
  </div>
</section>

<section class="piece card-back" aria-label="Business card back">
  <div class="map" role="img" aria-label="Dotted world map in dark olive tones"></div>
  <div class="logo"><span>tallowmere</span><span class="dot"></span></div>
</section>

<section class="piece letterhead" aria-label="Letterhead">
  <svg class="ring" width="513" height="609" viewBox="0 0 513 609">
    <circle cx="470" cy="568" r="98" fill="none" stroke="var(--sun)" stroke-width="13" stroke-dasharray="58 9"/>
    <circle cx="470" cy="568" r="82" fill="#ffffff" stroke="var(--line)" stroke-width="1"/>
  </svg>
  <div class="logo"><span>tallowmere</span><span class="dot"></span></div>
  <div class="letter">
    <div class="recipient">Mr. Owen Drayle<br>Customer Service Manager<br>Halvern Inc.<br>120 Corporate Blvd<br>Sometown, CO 80112</div>
    <p>Dear Mr. Drayle,</p>
    <p>I was excited to see your opening for a customer service rep, and I hope to be invited for an interview.</p>
    <p>My background includes serving as a customer service associate with a high-volume call center and retail setting. Most recently I worked as the customer service lead for a regional store, where I resolved requests, processed returns, trained new hires and handled escalated concerns with patience and a steady focus on keeping every customer satisfied.</p>
    <p>Previously, I worked within two large support teams, where I answered calls, tracked orders and solved a wide variety of issues. In these roles I consistently met my daily targets and kept a low error rate.</p>
    <p>In addition to this experience, I gained considerable customer service skills during part-time work and as a volunteer at a local shelter.</p>
    <p>Sincerely,</p>
    <div class="signature" role="img" aria-label="Handwritten signature"></div>
  </div>
  <div class="contact">
    4187 Larkwood Ave NE<br>Seattle, WA 98115<br>+1 (206) 555-0142<br>Vambeck.nora@<br>fenwistmail.com
  </div>
</section>

<section class="piece envelope-back" aria-label="Envelope back">
  <svg class="flap" width="510" height="195" viewBox="0 0 510 195">
    <rect x="0" y="0" width="510" height="36" fill="var(--charcoal)"/>
    <polygon points="0,36 510,36 510,40 255,92 0,40" fill="var(--charcoal-deep)"/>
  </svg>
  <span class="dot"></span>
</section>

<section class="piece envelope-front" aria-label="Envelope front">
  <svg class="ring" width="510" height="230" viewBox="0 0 510 230">
    <circle cx="458" cy="162" r="62" fill="none" stroke="var(--sun)" stroke-width="10" stroke-dasharray="38 7"/>
    <circle cx="458" cy="162" r="51" fill="#ffffff" stroke="var(--line)" stroke-width="1"/>
  </svg>
  <div class="logo"><span>tallowmere</span><span class="dot"></span></div>
</section>

<section class="piece compliment" aria-label="Compliment card">
  <div class="map" role="img" aria-label="Faint world map in light yellow tones"></div>
  <div class="logo"><span>tallowmere</span><span class="dot"></span></div>
</section>

</body>
</html>
```